Velvet Riot Rising Line of Sparkling Wine & Spirits

Back info: Nora Beth Quill Owner 555-318-4402 1480 E. Harlow Ave, Bldg. 2, & 3, Dunmere Ca. 95871
Sparkling Wines & Memorabilia www.velvetriotrising.com
Ok I have uploaded the winning design. The color that I am after is the Fushia, Raspberry, Red, Matte Satin Matalic Finish. With a 24 Karet Gold color Foil. The Bottle is on the top row and it's the 2nd Bottle in. That is the Color that I want. This is the style of font. Make sure that you put what we're advertising. Good Luck to you all. Warmest regards, Nora
21 & up UniSex
Sparkling Wine and Memorabilia
there listed up above.....

```html
<!DOCTYPE html>
<html lang="en">
<head>
<meta charset="utf-8">
<title>Velvet Riot Rising – Business Card</title>
<link href="https://fonts.googleapis.com/css2?family=Poppins:wght@400;500;600&family=Berkshire+Swash&display=swap" rel="stylesheet">
<style>
  :root {
    --backdrop: #2a2a2c;
    --raspberry-deep: #7a0033;
    --raspberry-mid: #8e0f45;
    --raspberry-glow: #d45a92;
    --gold: #e8ad2e;
    --gold-edge: #d89a16;
    --silver: #e4e4e8;
  }
  * { margin: 0; padding: 0; box-sizing: border-box; }
  html, body {
    width: 1200px; height: 689px; overflow: hidden;
    background: var(--backdrop);
  }
  .canvas {
    position: relative; width: 1200px; height: 689px;
    display: flex; align-items: center; justify-content: center; gap: 50px;
  }
  .card {
    position: relative; width: 525px; height: 300px;
    border-radius: 18px;
    border: 1.5px solid var(--gold-edge);
    background:
      linear-gradient(160deg, transparent 40%, rgba(212,90,146,0.55) 62%, transparent 80%),
      linear-gradient(135deg, var(--raspberry-deep) 0%, var(--raspberry-mid) 55%, var(--raspberry-deep) 100%);
    overflow: hidden;
    font-family: "Poppins", sans-serif;
  }
  /* Front */
  .card-front {
    display: flex; flex-direction: column; align-items: center; justify-content: center;
  }
  .brand-name {
    font-family: "Poppins", sans-serif;
    font-weight: 600; font-size: 42px; line-height: 1.1; color: var(--silver);
    letter-spacing: 0.5px;
  }
  .tagline {
    margin-top: 34px;
    font-weight: 500; font-size: 15px; letter-spacing: 1px;
    color: var(--gold); text-transform: uppercase;
  }
  /* Back */
  .card-back {
    display: flex; flex-direction: column; align-items: center; justify-content: center;
    color: var(--gold); text-align: center;
  }
  .owner-name {
    font-family: "Berkshire Swash", cursive;
    font-weight: 400; font-size: 30px; line-height: 1;
  }
  .owner-role { font-size: 14px; line-height: 1.2; margin-top: 2px; }
  .divider {
    width: 220px; height: 1px; background: var(--gold); margin: 12px 0;
  }
  .address { font-size: 15px; line-height: 1.3; }
  .contact-icons { display: flex; gap: 4px; margin-bottom: 6px; }
  .contact-icons svg { width: 18px; height: 18px; }
  .contact-line { font-size: 15px; line-height: 1.3; white-space: nowrap; }
</style>
</head>
<body>
<main class="canvas">
  <section class="card card-front">
    <h1 class="brand-name">Velvet Riot Rising</h1>
    <p class="tagline">Sparkling Wines &amp; Memorabilia</p>
  </section>

  <section class="card card-back">
    <h2 class="owner-name">Nora Beth Quill</h2>
    <p class="owner-role">Owner</p>
    <div class="divider"></div>
    <p class="address">1480 E. Harlow Ave, Bldg. 2, &amp; 3,<br>Dunmere Ca. 95871</p>
    <div class="divider"></div>
    <div class="contact-icons">
      <svg viewBox="0 0 20 20" aria-label="Phone">
        <circle cx="10" cy="10" r="10" fill="var(--gold)"/>
        <path d="M6.5 5.5l2 0 1 2.5-1.3 1a6 6 0 0 0 2.8 2.8l1-1.3 2.5 1v2c-4.5.5-8.5-3.5-8-8z" fill="var(--raspberry-deep)"/>
      </svg>
      <svg viewBox="0 0 20 20" aria-label="Email">
        <circle cx="10" cy="10" r="10" fill="var(--gold)"/>
        <rect x="5" y="6.5" width="10" height="7" fill="var(--raspberry-deep)"/>
        <path d="M5 6.5l5 4 5-4" fill="none" stroke="var(--gold)" stroke-width="1"/>
      </svg>
      <svg viewBox="0 0 20 20" aria-label="Website">
        <circle cx="10" cy="10" r="10" fill="var(--gold)"/>
        <g fill="none" stroke="var(--raspberry-deep)" stroke-width="1">
          <circle cx="10" cy="10" r="5"/>
          <ellipse cx="10" cy="10" rx="2.2" ry="5"/>
          <path d="M5 10h10M6 7.5h8M6 12.5h8"/>
        </g>
      </svg>
    </div>
    <p class="contact-line">555-318-4402</p>
    <p class="contact-line">hello@velvetriotrising.com</p>
    <p class="contact-line">www.velvetriotrising.com</p>
  </section>
</main>
</body>
</html>
```